Health Clinic treating people with mental illness needs a website

We need a website for a new mental health clinic based in Florida called Solvane Wellness USA. We treat people with mental health issues such as depression, PTSD, Bipolar, chronic pain, etc. I want the website to be easy to follow and inviting to the visitors. It should be easy to locate the different treatment options and how to go about contacting and making appointments. The images on the website should be something that the patients can relate to, whether a close up of a woman's face, something that conveys emotion. The patients visiting this website are often sad and miserable, they need to be able to feel comfortable when they look at this website. I want them to feel that we understand where they are coming from. I like colors such as purple, turquoise, lavender.

Target Market(s)

College students, veterans, anyone with mental illness

Industry/Entity Type

Health And Wellness

Font styles to use
Serif
Sans Serif

Colors

Designer to choose colors to be used in the design.

Requirements
Must have
• There should be a home/landing page, about us page, treatment page, contact page, and a FAQ page. I've included my logo below.
Nice to have
• The flow of the web pages should be calming and welcoming. I want people to feel warm and understood when they enter our page.
Should not have
• The images and writing should not be overly stimulating or aggressive.

```html
<!DOCTYPE html>
<html lang="en">
<head>
<meta charset="utf-8">
<title>Solvane Wellness USA</title>
<link href="https://fonts.googleapis.com/css2?family=Roboto:wght@400;500;700&display=swap" rel="stylesheet">
<style>
:root{
  --purple:#a94f9c;
  --purple-dark:#5a1f6e;
  --teal:#2aa58e;
  --blush:#fdeefb;
  --ink:#222;
  --text:#444;
  --line:#d9d9d9;
  --white:#fff;
}
*{margin:0;padding:0;box-sizing:border-box}
html,body{width:1200px;height:3594px;overflow:hidden}
body{position:relative;font-family:'Roboto',sans-serif;color:var(--ink);background:var(--white)}
.abs{position:absolute}
.btn{position:absolute;display:flex;align-items:center;justify-content:center;background:var(--teal);color:var(--white);border-radius:30px;font-weight:500;font-size:16px;text-transform:uppercase;white-space:nowrap}

/* header */
.header{left:0;top:0;width:1200px;height:110px;background:var(--white)}
.brand{left:91px;top:42px;font-size:22px;font-weight:500;color:var(--purple-dark);display:flex;align-items:center;gap:9px;white-space:nowrap}
.brand .dot{width:12px;height:12px;border-radius:50%;background:var(--purple)}
.nav{left:407px;top:47px;font-size:15px;font-weight:500}
.nav span{position:absolute;white-space:nowrap}
.nav .active{color:var(--purple)}
.phone{left:946px;top:44px;color:var(--purple);font-size:19px;font-weight:500;display:flex;align-items:center;gap:8px;white-space:nowrap}

/* hero */
.hero{left:0;top:110px;width:1200px;height:520px;background:linear-gradient(90deg,#d8b49a 0%,#e3cbbb 35%,#c9c3c0 60%,#b9b3ae 100%)}
.hero-name{left:520px;top:350px;width:589px;text-align:right;font-size:46px;font-weight:700;color:var(--purple-dark);line-height:1.1;white-space:nowrap}

/* about */
.about-photo{left:600px;top:630px;width:600px;height:623px;background:linear-gradient(135deg,#e9eef0 0%,#cfd8dc 45%,#b89a86 100%)}
.h2{font-size:30px;font-weight:500;color:var(--purple);white-space:nowrap}
.h3{font-size:22px;font-weight:400;color:var(--purple)}
.body-text{font-size:14.5px;line-height:24px;color:var(--text)}

/* treatment */
.treat{left:0;top:1253px;width:1200px;height:707px;background:var(--blush)}
.card{position:absolute;width:179px;height:179px;background:var(--white);box-shadow:4px 5px 8px rgba(0,0,0,.18);display:flex;flex-direction:column;align-items:center;justify-content:center;gap:14px;font-size:19px;color:var(--ink)}
.card svg{width:52px;height:52px;stroke:var(--purple);fill:none;stroke-width:2}
.card.on{background:var(--purple);color:#f1dcef}
.card.on svg{stroke:#f1dcef}

/* quote */
.quote{left:38px;top:2005px;width:1124px;height:315px;background:linear-gradient(90deg,#6d625b 0%,#8a817b 40%,#a8a39f 70%,#c9c6c3 100%)}
.quote-title{left:0;top:2088px;width:1200px;text-align:center;color:var(--white);font-size:54px;font-weight:700}

/* partners */
.center{left:0;width:1200px;text-align:center}
.badge{position:absolute;top:2622px;width:110px;height:52px;border-radius:6px;background:#cfcfcf}

/* contact */
.map{left:0;top:3143px;width:1200px;height:394px;background:linear-gradient(135deg,#e6e6e6 0%,#d6d6d6 50%,#e2e2e2 100%)}
.contact-card{left:153px;top:2836px;width:892px;height:433px;background:var(--white);box-shadow:0 0 6px rgba(0,0,0,.12)}
.contact-side{left:600px;top:2836px;width:445px;height:433px;background:var(--purple);color:var(--white)}
.field{position:absolute;border-bottom:1px solid var(--line);font-size:13px;color:#888;padding-bottom:6px}
.side-h{font-size:22px;font-weight:400}
.side-t{font-size:14.5px;line-height:24px;color:#f6e6f3;white-space:nowrap}

.footer{left:0;top:3537px;width:1200px;height:57px;background:var(--teal);color:var(--white);font-size:14px;display:flex;align-items:center;padding-left:91px}
</style>
</head>
<body>

<header class="abs header">
  <div class="abs brand"><span class="dot"></span>Solvane Wellness USA</div>
  <nav class="abs nav">
    <span class="active" style="left:0">HOME</span>
    <span style="left:81px">ABOUT US</span>
    <span style="left:191px">TREATMENT</span>
    <span style="left:318px">FAQ</span>
    <span style="left:385px">CONTACT US</span>
  </nav>
  <div class="abs phone">
    <svg width="16" height="16" viewBox="0 0 24 24" fill="#a94f9c"><path d="M6.6 10.8a15.1 15.1 0 0 0 6.6 6.6l2.2-2.2c.3-.3.7-.4 1-.2 1.1.4 2.3.6 3.6.6.6 0 1 .4 1 1V20c0 .6-.4 1-1 1A17 17 0 0 1 3 4c0-.6.4-1 1-1h3.5c.6 0 1 .4 1 1 0 1.3.2 2.5.6 3.6.1.3 0 .7-.2 1z"/></svg>
    +1 555 014 2290
  </div>
</header>

<section>
  <div class="abs hero" role="img" aria-label="Photo of a thoughtful woman resting her chin on her hand, a man blurred in the background"></div>
  <div class="abs hero-name">Solvane Wellness USA</div>
  <div class="btn" style="left:847px;top:474px;width:259px;height:53px;font-size:18px;font-weight:400">Book an Appointment</div>
</section>

<section>
  <h2 class="abs h2" style="left:91px;top:734px">About Solvane Wellness</h2>
  <p class="abs body-text" style="left:91px;top:797px;width:408px;text-align:justify">Lorem ipsum dolor sit amet, consectetur adipiscing elit, sed do eiusmod tempor incididunt ut labore et dolore magna aliqua. Ut enim ad minim veniam, quis nostrud exercitation ullamco laboris nisi ut aliquip ex ea commodo consequat. Duis aute irure dolor in reprehenderit in voluptate velit</p>
  <h3 class="abs h3" style="left:91px;top:958px">Opening Hours</h3>
  <p class="abs body-text" style="left:91px;top:996px">Mon : Friday - 9.00 am - 11.00 pm<br>Saturday - 10.00 am - 10.00 pm<br>Sunday -Closed</p>
  <div class="btn" style="left:92px;top:1114px;width:141px;height:46px">Read More</div>
  <div class="abs about-photo" role="img" aria-label="Photo of a doctor with a stethoscope listening to a worried young patient"></div>
</section>

<section>
  <div class="abs treat"></div>
  <h2 class="abs h2 center" style="top:1328px">Our Treatment</h2>

  <div class="card" style="left:219px;top:1403px"><svg viewBox="0 0 52 52"><rect x="6" y="14" width="18" height="22"/><circle cx="36" cy="16" r="5"/><path d="M30 38V26h12v12M28 44h20"/></svg>Depression</div>
  <div class="card" style="left:413px;top:1403px"><svg viewBox="0 0 52 52"><circle cx="26" cy="10" r="5"/><path d="M26 16v14M14 26l12 4 12-4M10 42c6-8 26-8 32 0"/></svg>PTSD</div>
  <div class="card on" style="left:607px;top:1403px"><svg viewBox="0 0 52 52"><path d="M6 16h22v12a11 11 0 0 1-22 0z"/><path d="M24 8h22v12a11 11 0 0 1-11 11"/><path d="M12 36c3-3 7-3 10 0"/></svg>Bipolar</div>
  <div class="card" style="left:801px;top:1403px"><svg viewBox="0 0 52 52"><circle cx="16" cy="8" r="4"/><path d="M12 16h8v26M36 14c6 4 8 14 4 24"/><circle cx="42" cy="38" r="3"/></svg>Chronic Pain</div>

  <div class="card" style="left:219px;top:1610px"><svg viewBox="0 0 52 52"><path d="M18 44V32c-6-4-8-10-6-16 3-9 20-10 26-2 4 6 2 12 2 16l4 4h-4v6h-8v6"/><path d="M24 28l4-8 4 8"/></svg>Lorem ipsum</div>
  <div class="card" style="left:413px;top:1610px"><svg viewBox="0 0 52 52"><path d="M18 44V32c-6-4-8-10-6-16 3-9 20-10 26-2 4 6 2 12 2 16l4 4h-4v6h-8v6"/><circle cx="26" cy="18" r="6"/></svg>Lorem ipsum</div>
  <div class="card" style="left:607px;top:1610px"><svg viewBox="0 0 52 52"><path d="M18 44V32c-6-4-8-10-6-16 3-9 20-10 26-2 4 6 2 12 2 16l4 4h-4v6h-8v6"/><rect x="21" y="13" width="10" height="10"/></svg>Lorem ipsum</div>
  <div class="card" style="left:801px;top:1610px"><svg viewBox="0 0 52 52"><path d="M18 44V32c-6-4-8-10-6-16 3-9 20-10 26-2 4 6 2 12 2 16l4 4h-4v6h-8v6"/><path d="M23 14l9 6-9 6z"/><path d="M26 2v4M8 10l3 3M44 10l-3 3"/></svg>Lorem ipsum</div>

  <div class="btn" style="left:529px;top:1832px;width:141px;height:44px">Read More</div>
</section>

<section>
  <div class="abs quote" role="img" aria-label="Photo of a pensive woman with her hand near her mouth in a dim room"></div>
  <h2 class="abs quote-title">Get a Free Quote</h2>
  <div class="btn" style="left:512px;top:2180px;width:176px;height:45px">Get Started</div>
</section>

<section>
  <h2 class="abs h2 center" style="top:2394px;font-size:34px">Our Partners</h2>
  <p class="abs center" style="top:2452px;font-size:21px">Lorem ipsum dolor sit amet, consectetur</p>
  <p class="abs body-text" style="left:200px;top:2497px;width:800px;text-align:center;font-size:15.5px;line-height:27px">Sed ut perspiciatis unde omnis iste natus error sit voluptatem accusantium doloremque laudantium, totam rem aperiam, eaque ipsa quae ab illo inventore veritatis et quasi architecto beatae vitae dicta sunt explicabo.</p>
  <div class="abs" style="left:193px;top:2577px;width:814px;height:1px;background:var(--line)"></div>
  <div class="badge" style="left:209px"></div>
  <div class="badge" style="left:381px"></div>
  <div class="badge" style="left:548px"></div>
  <div class="badge" style="left:717px"></div>
  <div class="badge" style="left:884px"></div>
  <div class="btn" style="left:512px;top:2708px;width:176px;height:45px">Get Started</div>
</section>

<section>
  <div class="abs map" role="img" aria-label="Map of the clinic location with a red pin marker"></div>
  <div class="abs contact-card"></div>
  <h2 class="abs h2" style="left:177px;top:2877px;font-size:32px">Contact</h2>
  <div class="field" style="left:181px;top:2944px;width:187px">Name</div>
  <div class="field" style="left:386px;top:2944px;width:187px">Email</div>
  <div class="field" style="left:181px;top:3007px;width:392px">Phone No</div>
  <div class="field" style="left:181px;top:3082px;width:392px;height:70px">Type Your Message here...</div>
  <div class="btn" style="left:178px;top:3177px;width:142px;height:45px">Submit</div>

  <div class="abs contact-side">
    <div class="abs side-h" style="left:29px;top:58px">Opening Hours</div>
    <p class="abs side-t" style="left:29px;top:96px">Mon : Friday - 9.00 am - 11.00 pm<br>Saturday - 10.00 am - 10.00 pm<br>Sunday -Closed</p>
    <div class="abs side-h" style="left:29px;top:220px">Address</div>
    <p class="abs side-t" style="left:29px;top:258px">Lorem ipsum dolor sit amet, consectetur</p>
    <p class="abs side-t" style="left:29px;top:306px">+1 555 014 2290<br>+1 555 014 7785<br>info@solvanewellness.com</p>
  </div>
</section>

<footer class="abs footer">© Copyrights.2019.Solvanewellness.All Rights Reserved</footer>

</body>
</html>
```